Plenko - Shoe Fitting App : Foot scanning app, 3D reconstruction and Fit recommandation.

We are a startup that has developed a 3D scanning App that compares the 3d reconstructed foot to the 3D Last (mould) of a shoe to find the best match and recommend a shoe size with a graphical representation of the fit on a reconstructed foot without texturing. The challenge of this app is to have a simple and intuitive onboarding of the user with clean and crisp ui and a simple tutorial for foot scanning. 3D representation of the fit is also key. What you see is what you feel is what we would like to achieve.

Target Market(s)

Sneaker Brands and athletic shoes brands

Industry/Entity Type

Footwear

Font styles to use
Other font styles liked:
• Oswald or Droid Serif

Colors
0094D4
00A9DD
6FCCEA
C7EBF8
E9F6FB

Requirements
Must have
• Simple intuitive UI to onboard the customer to scan his bare foot (please look at attached image on how to scan the foot). You must flip your phone so that the screen is facing your foot. Start at 40cm distance form the front of your foot and turn 360% slowly to capture the foot while you feel the aptic of the iPhone. That needs to be presented with a simple animation that the user can easily understand and skip if he is a returning customer and knows how to do that. the rest of the UI is to present the result of the scanned foot for the user to use to get his fit and size. The other must have is the final result screen. Where the user will a representation of the foot (snug, loose ) of different predefined areas of the foot so he can choose the fit that he likes and not necessarily the size that we suggest. Must match website design (https://www.plenko.example)
Nice to have
• An animation of the whole process (scan-compare 3d foot with 3d shoe last(or mould) and get the 3D result of the best fit + associated size. Optionaly, an option to play with your foot and transform it (avatar like with accessories and colours)
Should not have
• Too many colours. Too much text. No gender type. No race type.

```html
<!DOCTYPE html>
<html lang="en">
<head>
<meta charset="utf-8">
<title>Plenko – Foot Scanning Onboarding Screens</title>
<link href="https://fonts.googleapis.com/css2?family=Poppins:wght@300;400;500;600;700;800&display=swap" rel="stylesheet">
<style>
  :root {
    --canvas: #c8c8c8;
    --screen: #1a1a1a;
    --screen-alt: #222222;
    --ink: #ffffff;
    --black: #000000;
    --teal: #4bb3b4;
    --teal-dark: #2f6f70;
    --ring-1: #5e5e5e;
    --ring-2: #7a7a7a;
    --ring-3: #999999;
    --ring-4: #b9b9b9;
    --card-light: #efefef;
    --text-dark: #1a1a1a;
    --grey-chip: #7a7a7a;
    --dot-inactive: #2c2c2c;
    --dot-mid: #9a9a9a;
  }
  * { box-sizing: border-box; margin: 0; padding: 0; }
  html, body { width: 1200px; height: 627px; overflow: hidden; }
  body {
    background: var(--canvas);
    font-family: "Poppins", sans-serif;
    position: relative;
    color: var(--ink);
  }
  h2, h3 { font-weight: 400; }
  .screen {
    position: absolute;
    width: 206px;
    height: 418px;
    background: var(--screen);
  }
  .screen--light-check { left: 33.5px; top: 60px; }
  .screen--shoes { left: 263px; top: 60px; }
  .screen--scan { left: 490px; top: 59px; }
  .screen--review { left: 735px; top: 58px; }
  .screen--results { left: 966px; top: 58px; height: 513px; background: var(--screen-alt); }

  .brand {
    position: absolute;
    left: 0; right: 0;
    text-align: center;
    font-weight: 800;
    font-size: 22px;
    letter-spacing: 0.5px;
    line-height: 1;
  }
  .headline {
    position: absolute;
    left: 6px; right: 6px;
    text-align: center;
    font-size: 13.5px;
    line-height: 17px;
    font-weight: 400;
    text-transform: uppercase;
  }
  .headline strong { font-weight: 700; }

  .visual { position: absolute; border-radius: 50%; }
  .illustration {
    position: absolute;
    border-radius: 50%;
    background: radial-gradient(circle at 50% 45%, #ffffff 0%, #f2f2f2 60%, #dcdcdc 100%);
  }

  .btn {
    position: absolute;
    left: 20px;
    width: 167px;
    height: 30px;
    border-radius: 15px;
    background: var(--teal);
    color: var(--ink);
    font-weight: 700;
    font-size: 10px;
    letter-spacing: 0.2px;
    display: flex;
    align-items: center;
    justify-content: center;
    gap: 6px;
    text-transform: uppercase;
  }
  .btn--dark { background: var(--black); }
  .btn svg { width: 11px; height: 11px; }

  .pager { position: absolute; left: 0; right: 0; height: 14px; }
  .pager span {
    position: absolute;
    width: 11px; height: 11px;
    border-radius: 50%;
    background: var(--dot-mid);
  }

  .scan-note {
    position: absolute;
    left: 0; right: 0;
    text-align: center;
    font-weight: 600;
    font-size: 9.5px;
    line-height: 14px;
  }
  .foot-scan-area {
    position: absolute;
    left: 13px; top: 136px;
    width: 188px; height: 155px;
    border-radius: 40px 10px 60px 60px;
    background: radial-gradient(ellipse at 35% 55%, #000000 0%, #0b0b0b 60%, #1a1a1a 100%);
  }

  .review-text {
    position: absolute;
    left: 10px; right: 10px;
    top: 72px;
    text-align: center;
    font-weight: 700;
    font-size: 8.5px;
    line-height: 14px;
  }

  .card {
    position: absolute;
    left: 21px;
    width: 166px;
    border-radius: 6px;
  }
  .card--progress {
    top: 63px; height: 92px;
    background: var(--black);
    border: 1px solid #3a3a3a;
  }
  .card--fact { top: 170px; height: 151px; background: #ffffff; color: var(--text-dark); border: 1px solid #d0d0d0; }
  .card--prefs { left: 22px; top: 344px; height: 151px; background: var(--card-light); color: var(--text-dark); }

  .progress-title {
    position: absolute; left: 0; right: 0; top: 11px;
    text-align: center; font-size: 13.5px; line-height: 18px; text-transform: uppercase; font-weight: 400;
  }
  .progress-title strong { font-weight: 700; }
  .progress-value { position: absolute; left: 0; right: 0; top: 55px; text-align: center; font-size: 8px; font-weight: 700; }
  .progress-bar { position: absolute; left: 14px; right: 11px; top: 71px; height: 3.5px; background: var(--teal); border-radius: 2px; }

  .fact-title { position: absolute; left: 16px; top: 14px; font-size: 11px; line-height: 12px; text-transform: uppercase; font-weight: 400; }
  .fact-title strong { font-weight: 700; }
  .fact-icon {
    position: absolute; right: 14px; top: 12px; width: 38px; height: 32px;
    border-radius: 6px;
    background: linear-gradient(135deg, #f4f4f4, #dedede);
  }
  .fact-body { position: absolute; left: 16px; right: 8px; top: 52px; font-size: 6.2px; line-height: 11px; font-weight: 400; }
  .fact-body p + p { margin-top: 3px; }
  .btn--results { left: 36px; top: 136px; width: 96px; height: 26px; border-radius: 13px; font-size: 8px; }

  .prefs-title { position: absolute; left: 0; right: 0; top: 15px; text-align: center; font-size: 11.5px; line-height: 12.5px; text-transform: uppercase; font-weight: 400; }
  .prefs-title strong { font-weight: 700; }
  .prefs-question { position: absolute; left: 0; right: 0; top: 44px; text-align: center; font-size: 7.2px; }
  .chip {
    position: absolute; top: 71px;
    width: 36px; height: 36px; border-radius: 50%;
    display: flex; align-items: center; justify-content: center;
    font-size: 6.6px; font-weight: 700; color: var(--ink);
  }
  .chip--soft { left: 21px; background: var(--grey-chip); }
  .chip--medium { left: 66px; background: var(--black); }
  .chip--hard { left: 111px; background: var(--teal); }
  .chev { position: absolute; top: 84px; width: 7px; height: 9px; }
  .chev--prev { left: 9px; }
  .chev--next { right: 8px; }
  .prefs-hint { position: absolute; left: 8px; right: 8px; top: 114px; text-align: center; font-size: 6.4px; line-height: 11px; }
</style>
</head>
<body>

<!-- Step 1: lighting -->
<section class="screen screen--light-check">
  <div class="brand" style="top:32px">PLENKO</div>
  <h2 class="headline" style="top:72px">Make sure your’re in<br><strong>a well lit area</strong></h2>
  <svg class="visual" style="left:11px;top:117px" width="190" height="190" viewBox="0 0 190 190">
    <circle cx="95" cy="95" r="95" fill="var(--ring-1)"/>
    <circle cx="95" cy="95" r="83" fill="var(--ring-2)"/>
    <circle cx="95" cy="95" r="72" fill="var(--ring-3)"/>
    <circle cx="95" cy="95" r="66" fill="var(--ring-4)"/>
  </svg>
  <div class="illustration" role="img" aria-label="Line drawing of a glowing light bulb" style="left:45px;top:151px;width:122px;height:122px"></div>
  <div class="btn" style="top:319px">Next
    <svg viewBox="0 0 12 12"><path d="M1 6h9M6.5 2.5 10 6l-3.5 3.5" stroke="#fff" stroke-width="1.6" fill="none" stroke-linecap="round" stroke-linejoin="round"/></svg>
  </div>
  <div class="pager" style="top:372px">
    <span style="left:50px;top:7px;background:#fff;width:12px;height:12px"></span>
    <span style="left:75px;background:var(--dot-inactive)"></span>
    <span style="left:101px"></span>
    <span style="left:126px"></span>
  </div>
</section>

<!-- Step 2: remove shoes -->
<section class="screen screen--shoes">
  <div class="brand" style="top:32px">PLENKO</div>
  <h2 class="headline" style="top:72px">Take off your shoes<br><strong>and roll up pants</strong></h2>
  <svg class="visual" style="left:24px;top:125px" width="166" height="166" viewBox="0 0 166 166">
    <circle cx="83" cy="83" r="83" fill="var(--ring-1)"/>
  </svg>
  <div class="illustration" role="img" aria-label="Wireframe bare foot with a removed sneaker beside it" style="left:37px;top:138px;width:140px;height:140px"></div>
  <div class="btn" style="top:319px">Next
    <svg viewBox="0 0 12 12"><path d="M1 6h9M6.5 2.5 10 6l-3.5 3.5" stroke="#fff" stroke-width="1.6" fill="none" stroke-linecap="round" stroke-linejoin="round"/></svg>
  </div>
  <div class="pager" style="top:375px">
    <span style="left:71px"></span>
    <span style="left:93px;background:var(--dot-inactive)"></span>
    <span style="left:119px"></span>
  </div>
</section>

<!-- Step 3: scanning -->
<section class="screen screen--scan">
  <div class="brand" style="top:33px">PLENKO</div>
  <h2 class="headline" style="top:72px">Flip the screen<br><strong>toward your toes to<br>start scanning</strong></h2>
  <div class="foot-scan-area" role="img" aria-label="Dotted silhouette of a foot being scanned"></div>
  <svg style="position:absolute;left:88px;top:294px" width="32" height="22" viewBox="0 0 32 22">
    <text x="16" y="12" text-anchor="middle" font-family="Poppins, sans-serif" font-weight="700" font-size="10" fill="#fff">360</text>
    <circle cx="27.5" cy="3" r="1.8" fill="none" stroke="#fff" stroke-width="1"/>
    <path d="M4 9c-3 4 3 7 12 7s13-2 13-6" fill="none" stroke="#fff" stroke-width="1.2"/>
    <path d="M13 13.5l3 2.5-3 2.5" fill="none" stroke="#fff" stroke-width="1.2"/>
  </svg>
  <p class="scan-note" style="top:320px">scanned at 40 cm distance<br>at a low speed</p>
  <div class="btn" style="top:359px">Right foot
    <svg viewBox="0 0 12 12"><path d="M1 6h9M6.5 2.5 10 6l-3.5 3.5" stroke="#fff" stroke-width="1.6" fill="none" stroke-linecap="round" stroke-linejoin="round"/></svg>
  </div>
</section>

<!-- Step 4: reconstruction check -->
<section class="screen screen--review">
  <div class="brand" style="top:34px">PLENKO</div>
  <p class="review-text">Please check that the reconstruction<br>of your foot sems correct.</p>
  <svg class="visual" style="left:19px;top:111px" width="176" height="176" viewBox="0 0 176 176">
    <circle cx="88" cy="88" r="87" fill="none" stroke="var(--teal-dark)" stroke-width="1"/>
    <circle cx="88" cy="88" r="82" fill="#555"/>
    <circle cx="88" cy="88" r="72" fill="var(--ring-3)"/>
    <circle cx="88" cy="88" r="69" fill="none" stroke="var(--teal)" stroke-width="0.8"/>
  </svg>
  <div class="illustration" role="img" aria-label="Wireframe 3D reconstruction of a bare foot" style="left:46px;top:138px;width:122px;height:122px"></div>
  <svg style="position:absolute;left:92px;top:294px" width="30" height="20" viewBox="0 0 30 20">
    <path d="M1.5 10C6 3 24 3 28.5 10 24 17 6 17 1.5 10Z" fill="none" stroke="var(--teal)" stroke-width="2.2"/>
    <circle cx="15" cy="10" r="4.3" fill="none" stroke="var(--teal)" stroke-width="2.2"/>
  </svg>
  <div class="btn btn--dark" style="top:326px">Scan again
    <svg viewBox="0 0 12 12"><path d="M1 6h9M6.5 2.5 10 6l-3.5 3.5" stroke="#fff" stroke-width="1.6" fill="none" stroke-linecap="round" stroke-linejoin="round"/></svg>
  </div>
  <div class="btn" style="top:361px">My fit
    <svg viewBox="0 0 12 12"><path d="M1 6h9M6.5 2.5 10 6l-3.5 3.5" stroke="#fff" stroke-width="1.6" fill="none" stroke-linecap="round" stroke-linejoin="round"/></svg>
  </div>
</section>

<!-- Step 5: results & preferences -->
<section class="screen screen--results">
  <div class="brand" style="top:20px">PLENKO</div>

  <div class="card card--progress">
    <h2 class="progress-title">You’re all<br><strong>measured up</strong></h2>
    <div class="progress-value">100%</div>
    <div class="progress-bar"></div>
  </div>

  <div class="card card--fact">
    <h3 class="fact-title">Fun fact<br><strong>about feet</strong></h3>
    <div class="fact-icon" role="img" aria-label="Sketch of a rolled measuring tape"></div>
    <div class="fact-body">
      <p>Feet grow as we age - our arch may flatten causing our foot size to increase</p>
      <p>Click below to see how this shoe fits. Now that you’re scanned, you can quickly try other shoes without going through the process again</p>
    </div>
    <div class="btn btn--results">See results</div>
  </div>

  <div class="card card--prefs">
    <h3 class="prefs-title">Tell us your<br><strong>preference</strong></h3>
    <p class="prefs-question">How do you prfer the cushion?</p>
    <svg class="chev chev--prev" viewBox="0 0 7 9"><path d="M5.5 1 2 4.5 5.5 8" fill="none" stroke="#111" stroke-width="1.3"/></svg>
    <div class="chip chip--soft">SOFT</div>
    <div class="chip chip--medium">MEDIUM</div>
    <div class="chip chip--hard">HARD</div>
    <svg class="chev chev--next" viewBox="0 0 7 9"><path d="M1.5 1 5 4.5 1.5 8" fill="none" stroke="#111" stroke-width="1.3"/></svg>
    <p class="prefs-hint">Select an option to go to the next personal preference setting</p>
  </div>
</section>

</body>
</html>
```